Tolvik Commercial Cleaning is lookong for a new business card design.

A fresh new design that's professional and stylish. We need a serious upgrade to our business cards. I have included pictures of our existing ones. Our clients include professional individuals and business owners. We woupdblike something professional and upbeat. Please have fun and see what you come uo with.

Target Market(s)

Property managers, business owners, facility managers and other similar professionals

Industry/Entity Type

Janitorial

Contact Information for Business Card

Name, cell, office number, email, web address

Font styles to use
Sans Serif

Colors

Designer to choose colors to be used in the design.

Requirements
Must have
• please use the green color in our logo
Nice to have
• Bar code
Should not have
• Address

```html
<!DOCTYPE html>
<html lang="en">
<head>
<meta charset="utf-8">
<title>Tolvik Commercial Cleaning – Business Card</title>
<link href="https://fonts.googleapis.com/css2?family=Montserrat:wght@400;500;600&display=swap" rel="stylesheet">
<style>
  :root {
    --brand-green: #3fb34f;
    --brand-green-light: #52bd60;
    --card-white: #ffffff;
    --text-gray: #4a4a4a;
    --rule-gray: #cfd8cf;
    --backdrop: #7d6a55;
  }
  * { margin: 0; padding: 0; box-sizing: border-box; }
  html, body {
    width: 900px; height: 1200px; overflow: hidden;
    background: var(--backdrop);
    font-family: "Montserrat", sans-serif;
  }
  .stage { position: relative; width: 900px; height: 1200px; }
  .card {
    position: absolute; left: 66px; width: 768px; height: 453px;
    border-radius: 30px; overflow: hidden;
    box-shadow: 0 10px 28px rgba(0,0,0,0.35);
  }
  .card-front { top: 126px; background: var(--card-white); }
  .card-back { top: 642px; background: var(--brand-green); }

  .front-brand {
    position: absolute; right: 36px; top: 92px;
    color: var(--brand-green); font-weight: 600; font-size: 34px;
    letter-spacing: -0.3px;
  }
  .holder { position: absolute; left: 54px; top: 250px; }
  .holder-name { color: var(--brand-green); font-weight: 600; font-size: 30px; }
  .holder-title { color: var(--text-gray); font-size: 17px; margin-top: 4px; }
  .divider {
    position: absolute; left: 54px; right: 0; top: 328px;
    height: 2px; background: var(--rule-gray);
  }
  .contacts {
    position: absolute; left: 54px; top: 346px; list-style: none;
    color: var(--text-gray); font-size: 16px;
  }
  .contacts li { display: flex; align-items: center; gap: 12px; height: 26px; }
  .contacts svg { width: 15px; height: 15px; fill: var(--brand-green); }

  .back-watermark {
    position: absolute; left: 0; right: 0; top: 70px; text-align: center;
    color: var(--brand-green-light); font-weight: 600; font-size: 230px;
    letter-spacing: -6px; line-height: 1;
  }
  .back-brand {
    position: absolute; left: 0; right: 0; top: 198px; text-align: center;
    color: var(--card-white); font-weight: 600; font-size: 50px;
    letter-spacing: -0.5px;
  }
</style>
</head>
<body>
<main class="stage">
  <section class="card card-front">
    <div class="front-brand">Tolvik Commercial Cleaning</div>
    <div class="holder">
      <div class="holder-name">Mara Lindqvist</div>
      <div class="holder-title">CEO &amp; Founder</div>
    </div>
    <div class="divider"></div>
    <ul class="contacts">
      <li>
        <svg viewBox="0 0 24 24" aria-hidden="true"><path d="M6.6 10.8a15.1 15.1 0 0 0 6.6 6.6l2.2-2.2a1 1 0 0 1 1-.25 11.4 11.4 0 0 0 3.6.57 1 1 0 0 1 1 1V20a1 1 0 0 1-1 1A17 17 0 0 1 3 4a1 1 0 0 1 1-1h3.5a1 1 0 0 1 1 1c0 1.25.2 2.45.57 3.6a1 1 0 0 1-.25 1z"/></svg>
        (37) 555-0187
      </li>
      <li>
        <svg viewBox="0 0 24 24" aria-hidden="true"><path d="M2 5h20v14H2z M4 7v.4l8 5.2 8-5.2V7z" fill-rule="evenodd"/></svg>
        mara@tolvikcleaning.com
      </li>
      <li>
        <svg viewBox="0 0 24 24" aria-hidden="true"><path d="M12 2a10 10 0 1 0 0 20 10 10 0 0 0 0-20zm6.9 6h-2.9a15.7 15.7 0 0 0-1.4-3.6A8 8 0 0 1 18.9 8zM12 4a14 14 0 0 1 1.9 4h-3.8A14 14 0 0 1 12 4zM4.3 14a8 8 0 0 1 0-4h3.4a16.5 16.5 0 0 0 0 4zm.8 2h2.9a15.7 15.7 0 0 0 1.4 3.6A8 8 0 0 1 5.1 16zM8 8H5.1a8 8 0 0 1 4.3-3.6A15.7 15.7 0 0 0 8 8zm4 12a14 14 0 0 1-1.9-4h3.8A14 14 0 0 1 12 20zm2.3-6H9.7a14.7 14.7 0 0 1 0-4h4.6a14.7 14.7 0 0 1 0 4zm.3 5.6a15.7 15.7 0 0 0 1.4-3.6h2.9a8 8 0 0 1-4.3 3.6zm1.7-5.6a16.5 16.5 0 0 0 0-4h3.4a8 8 0 0 1 0 4z"/></svg>
        www.tolvikcleaning.com
      </li>
    </ul>
  </section>

  <section class="card card-back">
    <div class="back-watermark" aria-hidden="true">Tolvik</div>
    <div class="back-brand">Tolvik Commercial Cleaning</div>
  </section>
</main>
</body>
</html>
```